Creative, fresh business card design for Ripplecraft Facades

We need a fresh, creative business card design for Ripplecraft Facades. We are the manufacturer of Ripplecraft Facades in Australia. Wall panels are 2400 x 1200mm panels made from MDF and feature 3D patterns on the face of the panel. The colours to be used are green, silver/grey and white RGB
Red 187
Green 207
Blue 65.

An idea is to possibly use a watermark of one of our designs as a background (like on the "Grids" design on the left hand side of page 2 of our brochure).

Target Market(s)

Interior designers, architects, builders and home renovators

Industry/Entity Type

Business

Contact Information for Business Card

Details to go on the card are:
Our logo (attached),
Slogan: "Decorative panels for interiors and exteriors",
Contact name,
Position,
Mobile phone number,
Business address,
Business phone,
Business fax,
Website and
Email address.

I have attached a few images of our panels and our brochure for reference.

The colours of the business card should feature our logo colours which are: RGB
Red 187
Green 207
Blue 65

Requirements
Must have
• Very modern fonts and design. Some of the designs shown especially the "Prisms" design which is a popular design.
Nice to have
• Creative but simple design. Very contemporary.
Should not have
• Anything ornate or old fashioned.

```html
<!DOCTYPE html>
<html lang="en">
<head>
<meta charset="utf-8">
<title>Ripplecraft Facades – Business Card</title>
<link rel="stylesheet" href="https://fonts.googleapis.com/css2?family=Source+Sans+3:wght@300;400;600;700&display=swap">
<style>
  :root {
    --backdrop: #3a332f;
    --card: #0d0d0d;
    --lime: #bbcf41;
    --silver: #a9a9ad;
    --white: #f2f2f2;
    --rule: #1e1e1e;
  }
  * { margin: 0; padding: 0; box-sizing: border-box; }
  html, body { width: 1200px; height: 900px; overflow: hidden; }
  body {
    background: var(--backdrop);
    font-family: "Source Sans 3", Arial, sans-serif;
    position: relative;
  }
  .card {
    position: absolute;
    top: 295px;
    width: 540px;
    height: 310px;
    background: var(--card);
    border-radius: 3px;
    box-shadow: 0 14px 30px rgba(0,0,0,.55);
  }
  .card--back { left: 40px; }
  .card--front { left: 620px; }

  /* Back: brand + contact */
  .card--back .brand {
    position: absolute; left: 30px; top: 128px;
    display: flex; align-items: center; gap: 10px;
  }
  .brand__square { width: 22px; height: 22px; background: var(--lime); flex: none; }
  .brand__name {
    color: var(--white); font-weight: 600; font-size: 21px; letter-spacing: .2px;
    white-space: nowrap;
  }
  .divider {
    position: absolute; left: 262px; top: 20px; bottom: 20px;
    width: 1px; background: var(--rule);
  }
  .contact { position: absolute; left: 290px; top: 40px; color: var(--white); }
  .contact__name { color: var(--lime); font-weight: 700; font-size: 19px; line-height: 1.1; }
  .contact__role { font-size: 14px; margin-top: 2px; }
  .contact__address { font-size: 14px; line-height: 1.25; margin-top: 20px; }
  .contact__list { list-style: none; margin-top: 18px; }
  .contact__list li {
    display: flex; align-items: center; gap: 10px;
    font-size: 14.5px; line-height: 21px; white-space: nowrap;
  }
  .contact__list svg { width: 12px; height: 12px; fill: var(--lime); flex: none; }

  /* Front: brand + slogan */
  .card--front .brand {
    position: absolute; left: 0; right: 0; top: 112px;
    display: flex; justify-content: center; align-items: center; gap: 12px;
  }
  .card--front .brand__square { width: 28px; height: 28px; }
  .card--front .brand__name { font-size: 28px; }
  .slogan {
    position: absolute; left: 0; right: 0; top: 162px;
    text-align: center; color: var(--silver);
    font-weight: 300; font-size: 13px; letter-spacing: 2.2px; line-height: 1.3;
  }
</style>
</head>
<body>
  <section class="card card--back" aria-label="Business card, contact side">
    <div class="brand">
      <span class="brand__square"></span>
      <span class="brand__name">Ripplecraft Facades</span>
    </div>
    <div class="divider"></div>
    <div class="contact">
      <p class="contact__name">Marcus Hale</p>
      <p class="contact__role">Managing Director</p>
      <p class="contact__address">48 Kiln Street, Brookvale<br>NSW 2100, Australia</p>
      <ul class="contact__list">
        <li><svg viewBox="0 0 12 12"><path d="M3 0h6a1 1 0 0 1 1 1v10a1 1 0 0 1-1 1H3a1 1 0 0 1-1-1V1a1 1 0 0 1 1-1zm0 2v7h6V2z"/></svg>0412-555-018</li>
        <li><svg viewBox="0 0 12 12"><path d="M2.5 0l2 3-1.3 1.3a7 7 0 0 0 4.5 4.5L9 7.5l3 2-1.5 2.3C5 12 0 7 .2 1.5z"/></svg>(02)-5550-1843</li>
        <li><svg viewBox="0 0 12 12"><path d="M3 0h5v3H3zM1 4h10v8H1zm2 2v1h2V6zm4 0v1h2V6zM3 9v1h2V9zm4 0v1h2V9z"/></svg>(02)-5550-1844</li>
        <li><svg viewBox="0 0 12 12"><path d="M0 2h12v8H0zm1 1v.4l5 3.3 5-3.3V3z"/></svg>info@ripplecraft.example</li>
        <li><svg viewBox="0 0 12 12"><circle cx="6" cy="6" r="6"/></svg>www.ripplecraft.example</li>
      </ul>
    </div>
  </section>

  <section class="card card--front" aria-label="Business card, brand side">
    <div class="brand">
      <span class="brand__square"></span>
      <span class="brand__name">Ripplecraft Facades</span>
    </div>
    <p class="slogan">sculpted surfaces for<br>rooms &amp; open spaces</p>
  </section>
</body>
</html>
```